brovlanepass.net

Develop a website for brolanepass.net will be a site to sell tickets for concerts, shows, shows, theaters and others. I need a web design easy view, very easy to use and accumulate events by date. The aim is to develop the site was connected to a complex system that is already developed. (Important this page to a robust system was connected via links the idea is to develop only the front view)
Updates

Reason: I need more designs yet we have not made the decision

Target Market(s)

millennials, adults, who want to enjoy concerts and shows

Industry/Entity Type

Event

Number of Pages Required

5+ page

Colors
1b1b1b
aaaaaa
ffffff

Requirements
Must have
• Easy Vista, accumulation of upcoming events, past events. The tabs should have are: 1 Start: In this part of upcoming events occur. You could put a banner on the top and down the events by date. 2. How to order: page with instructions on how to purchase tickets 3. About Us: The company history 4. Contact: Phones and template for contact by mail 5. Our policies: shopping 6. Notice Privacy: Privacy Notice Copoy 7. Centers Sale: physical places where they can purchase tickets Promoters 8. access: Link to a template
Nice to have
• as you can see p www.quimbarostage.net or farunda.net or farunda.org or gallowmerk.net (important this page to a robust system was connected via links the idea is to develop only the front view)
Should not have
• Many things Tangled

```html
<!DOCTYPE html>
<html lang="en">
<head>
<meta charset="utf-8">
<title>Brovlane Pass — Tickets for concerts, shows and theaters</title>
<link rel="stylesheet" href="https://fonts.googleapis.com/css2?family=Raleway:wght@500;600;700;800&family=Open+Sans:ital,wght@0,400;0,600;0,700;1,400&display=swap">
<style>
:root{
  --ink:#1b1b1b;
  --grey:#aaaaaa;
  --white:#ffffff;
  --orange:#f8a11c;
  --line:#dddddd;
  --muted:#777777;
  --text:#555555;
}
*{box-sizing:border-box;margin:0;padding:0}
html,body{width:1200px;height:2413px;overflow:hidden}
body{position:relative;background:var(--white);font-family:"Open Sans",Arial,sans-serif;color:var(--ink)}
a{color:inherit;text-decoration:none}
.container{position:absolute;left:98px;width:1004px}

/* hero */
.hero{position:absolute;left:0;top:0;width:1200px;height:521px;
  background:radial-gradient(ellipse at 50% 30%,#8a7a6c 0%,#4a3e36 35%,#22201e 70%,#141414 100%)}
.hero-photo{position:absolute;inset:0;background:linear-gradient(180deg,rgba(0,0,0,0) 40%,rgba(20,14,10,.7) 100%)}
.topbar{position:absolute;left:0;top:0;width:1200px;height:35px;background:rgba(0,0,0,.55)}
.social-mini{position:absolute;left:98px;top:0;height:35px;display:flex;gap:14px;align-items:center}
.social-mini span{width:11px;height:11px;border-radius:2px;background:#dcdcdc}
.account{position:absolute;right:270px;top:0;height:35px;display:flex;align-items:center;gap:8px;font-size:13px;color:#eee}
.account i{display:inline-block;width:9px;height:9px;border-radius:50%;background:var(--orange);margin-right:5px;vertical-align:-1px}
.account .sep{color:#999}
.verified{position:absolute;left:931px;top:0;width:171px;height:35px;background:var(--grey);color:var(--white);
  font-style:italic;font-weight:600;font-size:14px;display:flex;align-items:center;justify-content:center;gap:8px}
.verified i{width:11px;height:11px;border-radius:50%;background:var(--orange)}
.brand{position:absolute;left:98px;top:58px;display:flex;align-items:center;gap:10px;color:var(--white);
  font-family:"Raleway",sans-serif;font-weight:700;font-size:22px;line-height:1.05}
.brand-mark{width:34px;height:34px;background:var(--orange)}
.main-nav{position:absolute;left:375px;top:72px;display:flex;gap:22px;font-size:15px;color:var(--white)}
.main-nav .active{color:var(--orange)}
.main-nav svg{margin-top:3px}
.hero-title{position:absolute;left:0;width:1200px;top:176px;text-align:center;color:var(--white);
  font-family:"Raleway",sans-serif;font-weight:800;font-size:66px;letter-spacing:1px}
.hero-sub{position:absolute;left:0;width:1200px;top:262px;text-align:center;color:#f2f2f2;font-size:22px}
.hero-btn{position:absolute;left:523px;top:315px;width:154px;height:37px;border:2px solid var(--white);border-radius:20px;
  color:var(--white);font-family:"Raleway",sans-serif;font-weight:700;font-size:14px;display:flex;align-items:center;justify-content:center;letter-spacing:.5px}
.dots{position:absolute;left:563px;top:469px;display:flex;gap:6px}
.dots span{width:13px;height:13px;border-radius:50%;border:2px solid var(--white)}
.dots .on{background:var(--white)}

/* categories */
.categories{position:absolute;left:0;top:521px;width:1200px;height:87px;background:var(--orange)}
.cat-list{position:absolute;left:82px;top:0;width:1036px;height:87px;display:flex}
.cat{flex:1;display:flex;align-items:center;justify-content:center;gap:16px;color:var(--white);
  font-family:"Raleway",sans-serif;font-weight:700;font-size:18px;border-right:1px solid rgba(255,255,255,.35)}
.cat:last-child{border-right:0}

/* events */
.section-title{position:absolute;left:0;width:1200px;text-align:center;font-family:"Raleway",sans-serif;font-weight:800;font-size:30px;color:var(--ink)}
.events{top:743px;display:grid;grid-template-columns:repeat(3,322px);column-gap:19px;row-gap:24px}
.event-card{height:290px;border:2px solid #e2e2e2;background:var(--white);padding:4px;position:relative}
.event-photo{height:218px}
.event-date{position:absolute;left:4px;top:4px;width:44px;padding:6px 0 6px 5px;background:var(--ink);color:var(--white);
  font-size:13px;font-weight:700;line-height:1.25}
.event-name{margin:8px 0 0 12px;font-family:"Raleway",sans-serif;font-weight:700;font-size:17px;color:var(--ink)}
.event-meta{margin:5px 0 0 12px;font-size:11.5px;font-style:italic;color:#999;display:flex;align-items:center;gap:6px}
.event-meta svg{flex:none}
.p1{background:linear-gradient(135deg,#3a2a20,#8a6a48 60%,#2a1f1a)}
.p2{background:linear-gradient(180deg,#e89a3a,#b5452c 45%,#2a2a70)}
.p3{background:radial-gradient(ellipse at 50% 55%,#8a4a3a,#1a0e0e 65%,#050505)}
.p4{background:linear-gradient(135deg,#1a1c4a,#5a5a9a 55%,#201a3a)}
.p5{background:linear-gradient(180deg,#3c3c3c,#8a8278 50%,#2a2a2a)}
.p6{background:linear-gradient(135deg,#c0502a,#6a2418 50%,#2a1a24)}
.p7{background:linear-gradient(135deg,#2a2a2a,#8a1a1a 55%,#1a1a1a)}
.p8{background:linear-gradient(135deg,#5a4a3a,#9a8a78 55%,#3a2a22)}
.p9{background:linear-gradient(135deg,#3a0808,#e0501a 50%,#6a1208)}
.view-more{position:absolute;left:512px;top:1707px;width:176px;height:38px;border:2px solid var(--line);border-radius:20px;
  color:var(--orange);font-family:"Raleway",sans-serif;font-weight:700;font-size:13px;display:flex;align-items:center;justify-content:center}
.divider{position:absolute;left:98px;top:1803px;width:1004px;height:1px;background:var(--line)}

/* guides */
.guides{top:1925px;display:flex;gap:12px}
.guide{width:191px;height:82px;border:2px solid #e2e2e2;display:flex;align-items:center;justify-content:center}
.guide span{width:120px;height:26px;background:#dcdcdc;border-radius:3px}
.arrow{position:absolute;top:1953px}

/* footer */
.footer{position:absolute;left:0;top:2066px;width:1200px;height:347px;border-top:3px solid var(--orange);background:var(--white)}
.foot-col{position:absolute;top:40px;height:200px}
.foot-col h4{font-family:"Raleway",sans-serif;font-weight:700;font-size:15px;color:var(--ink);margin-bottom:18px}
.foot-col li{list-style:none;font-size:11.5px;color:var(--text);line-height:26.5px}
.foot-sep{position:absolute;top:40px;width:1px;height:170px;background:#e6e6e6}
.foot-note{font-size:11.5px;color:var(--text);margin-bottom:16px}
.subscribe{display:flex;height:35px}
.subscribe .field{width:232px;border:1px solid #ccc;font-size:11.5px;color:var(--text);padding:9px 12px}
.subscribe .btn{width:93px;background:var(--orange);color:var(--white);font-size:12px;font-weight:700;display:flex;align-items:center;justify-content:center}
.stay{margin-top:28px}
.stay h4{margin-bottom:14px}
.social{display:flex;gap:10px}
.social span{width:32px;height:32px;border-radius:50%}
.copyright{position:absolute;left:98px;top:2348px;width:1004px;border-top:1px solid #e6e6e6;padding-top:22px;text-align:center;font-size:11.5px;color:var(--text)}
</style>
</head>
<body>

<header class="hero">
  <div class="hero-photo" role="img" aria-label="Concert crowd with raised hands under stage lights"></div>
  <div class="topbar">
    <div class="social-mini"><span></span><span></span><span></span><span></span><span></span><span></span></div>
    <div class="account">
      <a href="#"><i></i>Help</a><span class="sep">|</span>
      <a href="#"><i></i>My account</a><span class="sep">|</span>
      <a href="#"><i></i>Sign up</a>
    </div>
    <div class="verified"><i></i>Verified Tickets</div>
  </div>
  <div class="brand"><span class="brand-mark"></span><span>Brovlane<br>Pass</span></div>
  <nav class="main-nav">
    <a class="active" href="#">Home</a><a href="#">How to Order</a><a href="#">About us</a><a href="#">Contact us</a>
    <a href="#">Policies</a><a href="#">Privacy</a><a href="#">Center Sale</a><a href="#">Access</a>
    <svg width="14" height="14" viewBox="0 0 14 14"><circle cx="6" cy="6" r="4.5" fill="none" stroke="#fff" stroke-width="2"/><line x1="9.5" y1="9.5" x2="13" y2="13" stroke="#fff" stroke-width="2"/></svg>
  </nav>
  <h1 class="hero-title">BROVLANE PASS</h1>
  <p class="hero-sub">We want a site to sell tickets for concerts, shows, theaters and others</p>
  <a class="hero-btn" href="#">SEE TICKETS</a>
  <div class="dots"><span class="on"></span><span></span><span></span><span></span></div>
</header>

<section class="categories">
  <div class="cat-list">
    <div class="cat"><svg width="24" height="40" viewBox="0 0 24 40"><rect x="6" y="1" width="12" height="22" rx="6" fill="#fff"/><path d="M2 17a10 10 0 0 0 20 0" fill="none" stroke="#fff" stroke-width="2.5"/><line x1="12" y1="27" x2="12" y2="36" stroke="#fff" stroke-width="2.5"/><line x1="6" y1="37" x2="18" y2="37" stroke="#fff" stroke-width="2.5"/></svg>CONCERTS</div>
    <div class="cat"><svg width="44" height="44" viewBox="0 0 44 44"><circle cx="22" cy="22" r="20" fill="#fff"/><polygon points="22,14 29,19 26,27 18,27 15,19" fill="var(--orange)"/><circle cx="7" cy="18" r="4" fill="var(--orange)"/><circle cx="37" cy="18" r="4" fill="var(--orange)"/><circle cx="14" cy="36" r="4" fill="var(--orange)"/><circle cx="30" cy="36" r="4" fill="var(--orange)"/></svg>SPORTS</div>
    <div class="cat"><svg width="40" height="40" viewBox="0 0 40 40"><path d="M12 8 L36 2 V28" fill="none" stroke="#fff" stroke-width="4"/><line x1="12" y1="8" x2="12" y2="34" stroke="#fff" stroke-width="4"/><ellipse cx="7" cy="34" rx="7" ry="5" fill="#fff"/><ellipse cx="31" cy="28" rx="7" ry="5" fill="#fff"/></svg>MUSIC</div>
    <div class="cat"><svg width="48" height="34" viewBox="0 0 48 34"><rect x="0" y="2" width="32" height="30" rx="5" fill="#fff"/><polygon points="34,12 48,3 48,31 34,22" fill="#fff"/></svg>THEATERS</div>
    <div class="cat"><svg width="42" height="42" viewBox="0 0 42 42"><line x1="4" y1="38" x2="26" y2="16" stroke="#fff" stroke-width="6"/><line x1="27" y1="4" x2="27" y2="10" stroke="#fff" stroke-width="2.5"/><line x1="36" y1="15" x2="30" y2="15" stroke="#fff" stroke-width="2.5"/><line x1="34" y1="7" x2="30" y2="11" stroke="#fff" stroke-width="2.5"/><line x1="18" y1="5" x2="20" y2="10" stroke="#fff" stroke-width="2.5"/></svg>SHOWS</div>
  </div>
</section>

<h2 class="section-title" style="top:672px">UPCOMING EVENTS</h2>

<div class="container events">
  <article class="event-card"><div class="event-photo p1" role="img" aria-label="Guitarist playing to a crowd"></div><div class="event-date">26<br>nov<br>2017</div><h3 class="event-name">Finibus Bonorum et Malorum</h3><p class="event-meta"><svg width="10" height="10"><circle cx="5" cy="5" r="4" fill="none" stroke="#f8a11c" stroke-width="1.5"/></svg>10:00 PM <span>|</span><svg width="8" height="11" viewBox="0 0 8 11"><path d="M4 11C1 7 0 5.5 0 4a4 4 0 0 1 8 0c0 1.5-1 3-4 7z" fill="#f8a11c"/></svg>Blanditiis pra</p></article>
  <article class="event-card"><div class="event-photo p2" role="img" aria-label="Band on a brightly lit stage"></div><div class="event-date">26<br>nov<br>2017</div><h3 class="event-name">Finibus Bonorum et Malorum</h3><p class="event-meta"><svg width="10" height="10"><circle cx="5" cy="5" r="4" fill="none" stroke="#f8a11c" stroke-width="1.5"/></svg>10:00 PM <span>|</span><svg width="8" height="11" viewBox="0 0 8 11"><path d="M4 11C1 7 0 5.5 0 4a4 4 0 0 1 8 0c0 1.5-1 3-4 7z" fill="#f8a11c"/></svg>Blanditiis pra</p></article>
  <article class="event-card"><div class="event-photo p3" role="img" aria-label="Dance troupe performing on a dark stage"></div><div class="event-date">26<br>nov<br>2017</div><h3 class="event-name">Finibus Bonorum et Malorum</h3><p class="event-meta"><svg width="10" height="10"><circle cx="5" cy="5" r="4" fill="none" stroke="#f8a11c" stroke-width="1.5"/></svg>10:00 PM <span>|</span><svg width="8" height="11" viewBox="0 0 8 11"><path d="M4 11C1 7 0 5.5 0 4a4 4 0 0 1 8 0c0 1.5-1 3-4 7z" fill="#f8a11c"/></svg>Blanditiis pra</p></article>
  <article class="event-card"><div class="event-photo p4" role="img" aria-label="Singer with guitar under blue light"></div><div class="event-date">26<br>nov<br>2017</div><h3 class="event-name">Finibus Bonorum et Malorum</h3><p class="event-meta"><svg width="10" height="10"><circle cx="5" cy="5" r="4" fill="none" stroke="#f8a11c" stroke-width="1.5"/></svg>10:00 PM <span>|</span><svg width="8" height="11" viewBox="0 0 8 11"><path d="M4 11C1 7 0 5.5 0 4a4 4 0 0 1 8 0c0 1.5-1 3-4 7z" fill="#f8a11c"/></svg>Blanditiis pra</p></article>
  <article class="event-card"><div class="event-photo p5" role="img" aria-label="Jazz band with saxophones"></div><div class="event-date">26<br>nov<br>2017</div><h3 class="event-name">Finibus Bonorum et Malorum</h3><p class="event-meta"><svg width="10" height="10"><circle cx="5" cy="5" r="4" fill="none" stroke="#f8a11c" stroke-width="1.5"/></svg>10:00 PM <span>|</span><svg width="8" height="11" viewBox="0 0 8 11"><path d="M4 11C1 7 0 5.5 0 4a4 4 0 0 1 8 0c0 1.5-1 3-4 7z" fill="#f8a11c"/></svg>Blanditiis pra</p></article>
  <article class="event-card"><div class="event-photo p6" role="img" aria-label="DJ at the decks before a crowd"></div><div class="event-date">26<br>nov<br>2017</div><h3 class="event-name">Finibus Bonorum et Malorum</h3><p class="event-meta"><svg width="10" height="10"><circle cx="5" cy="5" r="4" fill="none" stroke="#f8a11c" stroke-width="1.5"/></svg>10:00 PM <span>|</span><svg width="8" height="11" viewBox="0 0 8 11"><path d="M4 11C1 7 0 5.5 0 4a4 4 0 0 1 8 0c0 1.5-1 3-4 7z" fill="#f8a11c"/></svg>Blanditiis pra</p></article>
  <article class="event-card"><div class="event-photo p7" role="img" aria-label="Magician performing an escape act"></div><div class="event-date">26<br>nov<br>2017</div><h3 class="event-name">Finibus Bonorum et Malorum</h3><p class="event-meta"><svg width="10" height="10"><circle cx="5" cy="5" r="4" fill="none" stroke="#f8a11c" stroke-width="1.5"/></svg>10:00 PM <span>|</span><svg width="8" height="11" viewBox="0 0 8 11"><path d="M4 11C1 7 0 5.5 0 4a4 4 0 0 1 8 0c0 1.5-1 3-4 7z" fill="#f8a11c"/></svg>Blanditiis pra</p></article>
  <article class="event-card"><div class="event-photo p8" role="img" aria-label="Horror theater scene with actors"></div><div class="event-date">26<br>nov<br>2017</div><h3 class="event-name">Finibus Bonorum et Malorum</h3><p class="event-meta"><svg width="10" height="10"><circle cx="5" cy="5" r="4" fill="none" stroke="#f8a11c" stroke-width="1.5"/></svg>10:00 PM <span>|</span><svg width="8" height="11" viewBox="0 0 8 11"><path d="M4 11C1 7 0 5.5 0 4a4 4 0 0 1 8 0c0 1.5-1 3-4 7z" fill="#f8a11c"/></svg>Blanditiis pra</p></article>
  <article class="event-card"><div class="event-photo p9" role="img" aria-label="Dancer in flowing red fabric"></div><div class="event-date">26<br>nov<br>2017</div><h3 class="event-name">Finibus Bonorum et Malorum</h3><p class="event-meta"><svg width="10" height="10"><circle cx="5" cy="5" r="4" fill="none" stroke="#f8a11c" stroke-width="1.5"/></svg>10:00 PM <span>|</span><svg width="8" height="11" viewBox="0 0 8 11"><path d="M4 11C1 7 0 5.5 0 4a4 4 0 0 1 8 0c0 1.5-1 3-4 7z" fill="#f8a11c"/></svg>Blanditiis pra</p></article>
</div>

<a class="view-more" href="#">VIEW MORE &gt;&gt;</a>
<div class="divider"></div>

<h2 class="section-title" style="top:1852px">ENTERTAINMENT GUIDES</h2>
<svg class="arrow" style="left:60px" width="16" height="26" viewBox="0 0 16 26"><polyline points="14,2 3,13 14,24" fill="none" stroke="#bbb" stroke-width="2.5"/></svg>
<div class="container guides">
  <div class="guide"><span></span></div><div class="guide"><span></span></div><div class="guide"><span></span></div><div class="guide"><span></span></div><div class="guide"><span></span></div>
</div>
<svg class="arrow" style="left:1124px" width="16" height="26" viewBox="0 0 16 26"><polyline points="2,2 13,13 2,24" fill="none" stroke="#bbb" stroke-width="2.5"/></svg>

<footer class="footer">
  <div class="foot-col" style="left:98px"><h4>RESOURCES</h4><ul><li>Your Account</li><li>Transfer or Sell Tickets</li><li>Print Tickets</li><li>FAQs</li><li>Refunds and Exchanges</li><li>Get Help</li></ul></div>
  <div class="foot-sep" style="left:280px"></div>
  <div class="foot-col" style="left:328px"><h4>HELP &amp; SUPPORT</h4><ul><li>Recommended Reading</li><li>Submit your Story</li><li>Contact Us</li><li>Frequently Asked Questions</li><li>How to Order</li></ul></div>
  <div class="foot-sep" style="left:531px"></div>
  <div class="foot-col" style="left:579px"><h4>QUICK LINKS</h4><ul><li>Livewell Stage</li><li>Hall of Embers</li><li>TixWeave</li><li>SeatsSoon</li><li>Eventglow</li><li>orbitra</li></ul></div>
  <div class="foot-sep" style="left:731px"></div>
  <div class="foot-col" style="left:777px">
    <h4>EMAIL SUBSCRIPTION</h4>
    <p class="foot-note">Register your email address to get information about us</p>
    <div class="subscribe"><div class="field">Email Address</div><div class="btn">SUBSCRIBE</div></div>
    <div class="stay"><h4>STAY CONNECTED</h4>
      <div class="social"><span style="background:#5cb85c"></span><span style="background:#3b5998"></span><span style="background:#4aa3df"></span><span style="background:#dd4b39"></span><span style="background:#4d7da6"></span><span style="background:#6fa8dc"></span><span style="background:#cc181e"></span><span style="background:#c8232c"></span></div>
    </div>
  </div>
</footer>
<p class="copyright">Copyrights © 2017, Brovlane Pass. All Rights Reserved &nbsp;|&nbsp; Privacy Policy | Terms of Use | Feedback</p>

</body>
</html>
```